Veltrano.co - Polar Expeditions Specialists

We need a modern, visually striking business card for Veltrano.co, a company specialized in selling expedition cruises to the most remote regions on Earth, with a focus on the Arctic and Antarctica. The design should instantly communicate that the cardholder is an expert in polar travel. Use clean, premium aesthetics with cool tones like icy blue and white, possibly incorporating polar imagery (ice, glaciers, penguins, etc.)

Attached the logo

Contact Information for Business Card

Feels high-end and trustworthy.. Visually memorable — encourages people to keep it

Colors
0054AA
0677BA
7BADD7
CADEEF
E8F1F8

Requirements
Must have
• ice, glaciers, penguins, montains
Nice to have
• modern, transparente,

```html
<!DOCTYPE html>
<html lang="en">
<head>
<meta charset="utf-8">
<title>Veltrano.co – Business Card</title>
<link rel="stylesheet" href="https://fonts.googleapis.com/css2?family=Poppins:wght@600;700&family=Arimo:wght@400;700&display=swap">
<style>
  :root {
    --page-bg: #dcdcdc;
    --card-front: #f4f4f6;
    --brand-blue: #306dab;
    --ink: #1f1f1f;
    --muted: #555555;
    --band-gray: #606060;
    --white: #ffffff;
  }
  * { box-sizing: border-box; margin: 0; padding: 0; }
  html, body { width: 1200px; height: 1040px; overflow: hidden; }
  body { background: var(--page-bg); font-family: "Arimo", Arial, sans-serif; position: relative; }

  .card {
    position: absolute;
    width: 642px;
    height: 368px;
    border-radius: 16px;
    overflow: hidden;
  }
  .card-front { left: 285px; top: 129px; background: var(--card-front); }
  .card-back  { left: 285px; top: 567px; background: var(--brand-blue); }

  .brand-mark { display: block; margin: 0 auto; border-radius: 50%; }

  .brand-front {
    position: absolute;
    right: 43px;
    top: 40px;
    text-align: center;
    color: var(--brand-blue);
    font-family: "Poppins", Arial, sans-serif;
  }
  .brand-front .brand-mark { width: 60px; height: 60px; background: var(--brand-blue); margin-bottom: 12px; }
  .brand-front .brand-name { font-size: 34px; font-weight: 700; line-height: 1; letter-spacing: 0.2px; }
  .brand-front .brand-tagline { font-size: 11px; font-weight: 600; margin-top: 6px; }

  .holder { position: absolute; left: 45px; top: 203px; }
  .holder-name { font-size: 25px; font-weight: 700; color: var(--brand-blue); line-height: 1.1; }
  .holder-title { font-size: 15px; color: var(--muted); margin-top: 3px; }

  .divider {
    position: absolute;
    left: 45px;
    right: 43px;
    top: 256px;
    height: 1px;
    background: var(--ink);
  }

  .contact-list { position: absolute; left: 45px; top: 268px; list-style: none; }
  .contact-list li {
    display: flex;
    align-items: center;
    gap: 8px;
    font-size: 16px;
    color: var(--ink);
    height: 20px;
  }
  .contact-list svg { width: 13px; height: 13px; flex: none; fill: var(--brand-blue); }

  .address {
    position: absolute;
    right: 43px;
    top: 270px;
    text-align: right;
    font-size: 16px;
    line-height: 20px;
    color: var(--ink);
  }

  .band { position: absolute; left: 0; right: 0; bottom: 0; height: 18px; background: var(--band-gray); }
  .band-blue {
    position: absolute;
    left: -10px;
    top: 0;
    bottom: 0;
    width: 427px;
    background: var(--brand-blue);
    transform: skewX(-14deg);
    border-right: 3px solid var(--white);
  }

  .brand-back {
    position: absolute;
    left: 0;
    right: 0;
    top: 82px;
    text-align: center;
    color: var(--white);
    font-family: "Poppins", Arial, sans-serif;
  }
  .brand-back .brand-mark { width: 86px; height: 86px; background: var(--white); margin-bottom: 20px; }
  .brand-back .brand-name { font-size: 48px; font-weight: 700; line-height: 1; }
  .brand-back .brand-tagline { font-size: 16px; font-weight: 600; margin-top: 6px; }
</style>
</head>
<body>

<section class="card card-front" aria-label="Business card front">
  <div class="brand-front">
    <span class="brand-mark" aria-hidden="true"></span>
    <div class="brand-name">Veltrano.co</div>
    <div class="brand-tagline">Polar Expeditions Specialists</div>
  </div>

  <div class="holder">
    <div class="holder-name">Marcus Hale</div>
    <div class="holder-title">President</div>
  </div>

  <div class="divider"></div>

  <ul class="contact-list">
    <li>
      <svg viewBox="0 0 24 24" aria-hidden="true"><path d="M6.6 10.8a15.1 15.1 0 0 0 6.6 6.6l2.2-2.2c.3-.3.7-.4 1-.2 1.1.4 2.3.6 3.6.6.6 0 1 .4 1 1V20c0 .6-.4 1-1 1A17 17 0 0 1 3 4c0-.6.4-1 1-1h3.5c.6 0 1 .4 1 1 0 1.3.2 2.5.6 3.6.1.3 0 .7-.2 1z"/></svg>
      (415) 2904-6618
    </li>
    <li>
      <svg viewBox="0 0 24 24" aria-hidden="true"><path d="M2 5h20v14H2z M3.5 6.5 12 13l8.5-6.5" fill="none" stroke="#306dab" stroke-width="2"/></svg>
      hello@veltrano.co
    </li>
    <li>
      <svg viewBox="0 0 24 24" aria-hidden="true"><circle cx="12" cy="12" r="10"/><path d="M5 9c3 0 4 2 3 4s1 4 2 6M14 3c-1 2 1 3 3 3s3 3 2 5" fill="none" stroke="#ffffff" stroke-width="1.6"/></svg>
      www.veltrano.co
    </li>
  </ul>

  <div class="address">
    2716 Harbor Crest Lane<br>
    Bayview, ME 04609
  </div>

  <div class="band"><div class="band-blue"></div></div>
</section>

<section class="card card-back" aria-label="Business card back">
  <div class="brand-back">
    <span class="brand-mark" aria-hidden="true"></span>
    <div class="brand-name">Veltrano.co</div>
    <div class="brand-tagline">Polar Expeditions Specialists</div>
  </div>
</section>

</body>
</html>
```